Design a Mobile App for Landscape Businesses

This project is to design the first three screens for a mobile app for Landscape and Lawncare businesses. This app will serve as a directory for homeowners to locate landscape and lawn care businesses and for landscape businesses and contractors to run their business. See the attached PDF for more information and example
Here is the link to the description https://lnkbrev.example/q7z3Kp

Target Market(s)

Landscape and lawn care business, gardeners, home owners

Industry/Entity Type

Landscape Gardening

Logo Text

Verdalink

Colors

Designer to choose colors to be used in the design.

```html
<!DOCTYPE html>
<html lang="en">
<head>
<meta charset="utf-8">
<title>Verdalink — Welcome</title>
<link href="https://fonts.googleapis.com/css2?family=Montserrat:wght@400;500;600&display=swap" rel="stylesheet">
<style>
  :root {
    --page-bg: #efefef;
    --grass-top: #3cbf7f;
    --grass-mid: #35b86f;
    --grass-low: #3fc46a;
    --grass-deep: #2aa871;
    --badge: #17a36b;
    --white: #ffffff;
    --button-text: #17a060;
  }
  * { box-sizing: border-box; margin: 0; padding: 0; }
  html, body {
    width: 1200px;
    height: 1200px;
    overflow: hidden;
    background: var(--page-bg);
    font-family: "Montserrat", sans-serif;
  }
  .screen {
    position: absolute;
    left: 283px;
    top: 40px;
    width: 634px;
    height: 1120px;
    overflow: hidden;
    color: var(--white);
  }
  .screen__backdrop {
    position: absolute;
    inset: 0;
    background:
      radial-gradient(ellipse at 30% 75%, rgba(80, 210, 100, 0.45), transparent 60%),
      radial-gradient(ellipse at 80% 30%, rgba(70, 200, 150, 0.35), transparent 55%),
      linear-gradient(180deg, var(--grass-top) 0%, var(--grass-mid) 45%, var(--grass-low) 75%, var(--grass-deep) 100%);
  }
  .status-bar {
    position: absolute;
    top: 20px;
    left: 22px;
    right: 22px;
    height: 24px;
    display: flex;
    align-items: center;
    justify-content: space-between;
    font-size: 18px;
    font-weight: 500;
  }
  .status-bar__time {
    position: absolute;
    left: 50%;
    transform: translateX(-50%);
  }
  .status-bar__group { display: flex; align-items: center; gap: 6px; }
  .brand-badge {
    position: absolute;
    left: 166px;
    top: 258px;
    width: 304px;
    height: 304px;
    border-radius: 50%;
    background: var(--badge);
    display: flex;
    align-items: center;
    justify-content: center;
  }
  .brand-badge__name {
    font-size: 38px;
    font-weight: 500;
    letter-spacing: 0.5px;
    color: var(--white);
  }
  .intro {
    position: absolute;
    top: 638px;
    left: 0;
    right: 0;
    text-align: center;
    font-size: 17px;
    line-height: 21px;
    font-weight: 400;
  }
  .pager {
    position: absolute;
    top: 770px;
    left: 0;
    right: 0;
    display: flex;
    justify-content: center;
    gap: 28px;
  }
  .pager__dot {
    width: 17px;
    height: 17px;
    border-radius: 50%;
    border: 1px solid rgba(255, 255, 255, 0.8);
  }
  .pager__dot--active { background: rgba(255, 255, 255, 0.85); border-color: transparent; }
  .actions {
    position: absolute;
    top: 990px;
    left: 59px;
    right: 64px;
    display: flex;
    justify-content: space-between;
  }
  .button {
    width: 236px;
    height: 62px;
    border-radius: 31px;
    display: flex;
    align-items: center;
    justify-content: center;
    font-size: 17px;
    font-weight: 600;
    letter-spacing: 0.3px;
    text-transform: uppercase;
  }
  .button--solid { background: var(--white); color: var(--button-text); }
  .button--outline { border: 1.5px solid var(--white); color: var(--white); }
</style>
</head>
<body>
  <main class="screen">
    <div class="screen__backdrop" role="img" aria-label="Close-up photo of fresh green grass blades, softly blurred"></div>

    <header class="status-bar">
      <div class="status-bar__group">
        <svg width="58" height="14" viewBox="0 0 58 14" aria-hidden="true">
          <circle cx="6" cy="7" r="5" fill="#fff"/>
          <circle cx="17" cy="7" r="5" fill="#fff"/>
          <circle cx="28" cy="7" r="5" fill="#fff"/>
          <circle cx="39" cy="7" r="4.3" fill="none" stroke="#fff" stroke-width="1"/>
          <circle cx="50" cy="7" r="4.3" fill="none" stroke="#fff" stroke-width="1"/>
        </svg>
        <svg width="22" height="16" viewBox="0 0 22 16" aria-hidden="true">
          <path d="M2 6a13 13 0 0 1 18 0" fill="none" stroke="#fff" stroke-width="2.2" stroke-linecap="round"/>
          <path d="M5.5 9.5a8 8 0 0 1 11 0" fill="none" stroke="#fff" stroke-width="2.2" stroke-linecap="round"/>
          <circle cx="11" cy="13.5" r="2" fill="#fff"/>
        </svg>
      </div>
      <span class="status-bar__time">4:21 PM</span>
      <div class="status-bar__group">
        <svg width="12" height="20" viewBox="0 0 12 20" aria-hidden="true">
          <path d="M1.5 5.5l9 8.5-4.5 4V2l4.5 4-9 8.5" fill="none" stroke="#fff" stroke-width="1.3"/>
        </svg>
        <span>100%</span>
        <svg width="40" height="18" viewBox="0 0 40 18" aria-hidden="true">
          <rect x="1" y="1" width="34" height="16" rx="2" fill="none" stroke="#fff" stroke-width="2"/>
          <rect x="4" y="4" width="19" height="10" fill="#fff"/>
          <rect x="36" y="6" width="3" height="6" fill="#fff"/>
        </svg>
      </div>
    </header>

    <div class="brand-badge">
      <span class="brand-badge__name">Verdalink</span>
    </div>

    <p class="intro">Verdalink is a mobile app for running<br>Landscape and Lawncare business.</p>

    <nav class="pager" aria-label="Intro pages">
      <span class="pager__dot"></span>
      <span class="pager__dot pager__dot--active"></span>
      <span class="pager__dot"></span>
    </nav>

    <div class="actions">
      <span class="button button--solid">Sign in</span>
      <span class="button button--outline">Sign up</span>
    </div>
  </main>
</body>
</html>
```